Tovimar Community Development Planning New web site

Design a new web site. I have a budget of $1,500.00.
Attached on PowerPoint is a complete site plan. Home page and linked pages.
10 - 12 pages. All copy and photos will be supplied. (300dpi)
I have shown them the concept which they like.
No data bases required. Home page with animations dissolving.
They former web site has been taken down. They have been in business 30 years in New Jersey
Colors teal blues and greens
There will be a new logo)being designed)
The text in home page copy will give you a detailed story what they are all about.

files have been approved for Tovimar, Inc.   Brenton is the designer

```html
<!DOCTYPE html>
<html lang="en">
<head>
<meta charset="utf-8">
<title>Tovimar Inc – Conduct Placement Lotteries</title>
<link rel="stylesheet" href="https://fonts.googleapis.com/css2?family=Montserrat:wght@600&family=Mulish:wght@400;500&family=Open+Sans:wght@400&display=swap">
<style>
  :root {
    --hero-light: #b9dca0;
    --hero-mid: #9ccb82;
    --hero-deep: #7fae69;
    --title-shadow: #2f5a12;
    --white: #ffffff;
    --accent-yellow: #eef000;
    --nav-bg: #0e0f0d;
    --nav-active: #5cb135;
    --brand-green: #5cb135;
    --menu-text: #4f9a2c;
    --ink: #1e1e1e;
  }
  * { box-sizing: border-box; margin: 0; padding: 0; }
  html, body { width: 1200px; height: 716px; overflow: hidden; background: var(--nav-bg); }
  .page { position: relative; width: 1200px; height: 716px; overflow: hidden; }

  .hero {
    position: absolute; left: 0; top: 0; width: 1200px; height: 646px;
    background: linear-gradient(160deg, var(--hero-light) 0%, var(--hero-mid) 55%, var(--hero-deep) 100%);
  }

  .social { position: absolute; top: 12px; right: 46px; display: flex; gap: 7px; }
  .social span { width: 22px; height: 22px; border: 1px solid var(--white); border-radius: 50%; display: block; }

  .ornament { position: absolute; left: 410px; top: 143px; width: 381px; height: 48px; }

  .hero-title {
    position: absolute; left: 0; top: 203px; width: 1200px; text-align: center;
    font-family: "Montserrat", sans-serif; font-weight: 600; font-size: 60px;
    letter-spacing: 0.5px; color: var(--white);
    text-shadow: 2px 2px 0 var(--title-shadow), 3px 3px 0 var(--title-shadow);
  }
  .hero-lead {
    position: absolute; left: 250px; top: 284px; width: 700px; text-align: center;
    font-family: "Mulish", sans-serif; font-weight: 500; font-size: 23px; line-height: 29px;
    color: var(--white); text-shadow: 1px 1px 2px rgba(40,70,20,0.6);
  }
  .cta {
    position: absolute; left: 485px; top: 383px; width: 230px; height: 52px;
    background: var(--accent-yellow); border: 1px solid #3a3a10;
    display: flex; align-items: center; justify-content: center; gap: 18px;
    font-family: "Mulish", sans-serif; font-size: 18px; color: var(--ink); text-decoration: none;
  }

  .town-menu {
    position: absolute; left: 576px; top: 488px; width: 125px; height: 136px;
    background: #f7f9f4; box-shadow: 0 2px 6px rgba(0,0,0,0.25);
    padding: 19px 0 0 21px; list-style: none;
  }
  .town-menu li {
    font-family: "Open Sans", sans-serif; font-size: 13px; color: var(--menu-text);
    line-height: 26.5px;
  }
  .town-menu::after {
    content: ""; position: absolute; left: 15px; bottom: -9px;
    border-left: 9px solid transparent; border-right: 9px solid transparent;
    border-top: 9px solid #f7f9f4;
  }

  .site-nav {
    position: absolute; left: 0; top: 646px; width: 1200px; height: 70px;
    background: var(--nav-bg); display: flex; align-items: center; padding: 0 45px 0 44px;
  }
  .brand { display: flex; align-items: center; gap: 9px; }
  .brand-mark { width: 33px; height: 33px; border: 1px solid var(--white); border-radius: 50%; }
  .brand-name {
    font-family: "Mulish", sans-serif; font-weight: 400; font-size: 27px; color: var(--brand-green);
    letter-spacing: 0.3px;
  }
  .nav-links { margin-left: auto; display: flex; gap: 18px; list-style: none; }
  .nav-links li {
    font-family: "Mulish", sans-serif; font-size: 16px; color: var(--white); letter-spacing: 0.2px;
  }
  .nav-links li.is-active { color: var(--nav-active); }
</style>
</head>
<body>
<div class="page">
  <section class="hero" role="img" aria-label="Photo of hands drafting architectural floor plans with a pencil and ruler, tinted green"></section>

  <div class="social" aria-label="Social links"><span></span><span></span><span></span></div>

  <svg class="ornament" viewBox="0 0 381 48" aria-hidden="true">
    <line x1="0" y1="24" x2="167" y2="24" stroke="#ffffff" stroke-width="1"/>
    <line x1="214" y1="24" x2="381" y2="24" stroke="#ffffff" stroke-width="1"/>
    <circle cx="190.5" cy="24" r="23" fill="none" stroke="#ffffff" stroke-width="1"/>
  </svg>

  <h1 class="hero-title">CONDUCT PLACEMENT LOTTERIES</h1>
  <p class="hero-lead">Explain implementation of a lottery and select applicants and keep you out of that process</p>

  <a class="cta" href="#">CALL TO ACTION
    <svg width="10" height="12" viewBox="0 0 10 12" aria-hidden="true"><path d="M2 1 L7 6 L2 11" fill="none" stroke="#1e1e1e" stroke-width="2.4"/></svg>
  </a>

  <ul class="town-menu">
    <li>LAKEWOOD</li>
    <li>BRICK</li>
    <li>JACKSON</li>
    <li>WARREN</li>
  </ul>

  <nav class="site-nav">
    <div class="brand">
      <span class="brand-mark"></span>
      <span class="brand-name">TOVIMAR INC</span>
    </div>
    <ul class="nav-links">
      <li>HOME</li>
      <li>COMPANY</li>
      <li>SERVICES</li>
      <li class="is-active">HOUSING REHAB APPLICATION</li>
      <li>AFFORDABLE APPLICATION</li>
      <li>CONTACT US</li>
    </ul>
  </nav>
</div>
</body>
</html>
```